HR services to some of biggest Silicon Valley Tech companies needs a new website

We need a new website design probably 4-5 pages initially. Here are some websites we like the look of https://quenmarport.com/ , https://www.vribly.com/ and https://fennix.com/ .

Target Market(s)

Silicon valley tech companies

Industry/Entity Type

HR

Coding

Coded - Design and coding required

Number of Pages Required

5+ page

Requirements
Nice to have
• any stock photos or images should show a diverse group of people. Our client base is very diverse

```html
<!DOCTYPE html>
<html lang="en">
<head>
<meta charset="utf-8">
<title>HR Tandem Consulting</title>
<link rel="stylesheet" href="https://fonts.googleapis.com/css2?family=Poppins:wght@300;400;500;600;700&display=swap">
<style>
:root{
  --yellow:#fcc800;
  --ink:#111111;
  --dark:#1c1c1c;
  --grey:#4a4a4a;
  --muted:#6b6b6b;
  --line:#d9d9d9;
  --white:#ffffff;
  --pale:#f4f4f4;
}
*{box-sizing:border-box;margin:0;padding:0}
html,body{width:1200px;height:4785px;overflow:hidden}
body{font-family:"Poppins",sans-serif;color:var(--ink);background:var(--white);position:relative}
section,header,footer{position:absolute;left:0;width:1200px;overflow:hidden}
.abs{position:absolute}
.btn{position:absolute;display:flex;align-items:center;justify-content:center;background:var(--yellow);color:var(--ink);font-weight:600;font-size:11px;border-radius:26px;letter-spacing:.3px;text-transform:uppercase}
.photo{position:absolute;inset:0}

/* hero */
.hero{top:0;height:600px}
.hero .photo{background:linear-gradient(100deg,#3b2e22 0%,#6b5540 40%,#a88a66 65%,#5a4a3a 100%)}
.hero .shade{position:absolute;inset:0;background:linear-gradient(90deg,rgba(0,0,0,.55),rgba(0,0,0,.1) 70%)}
.brand{position:absolute;left:78px;top:34px;display:flex;align-items:center;gap:10px;color:var(--white);font-weight:500;font-size:15px;letter-spacing:.5px}
.brand i{width:30px;height:30px;border:2px solid var(--yellow);border-radius:50%}
.nav{position:absolute;left:328px;top:40px;display:flex;gap:33px;font-size:13px;color:var(--white)}
.nav .on{color:var(--yellow);border-bottom:2px solid var(--yellow);padding-bottom:8px}
.hero h1{position:absolute;left:143px;top:205px;font-size:38px;line-height:51px;color:var(--white);font-weight:700}
.hero h1 b{color:var(--yellow)}
.hero .sub{position:absolute;left:143px;top:316px;color:var(--white);font-size:19px;font-weight:300}
.play{position:absolute;left:350px;top:378px;width:48px;height:48px;border:2px solid var(--yellow);border-radius:50%;display:flex;align-items:center;justify-content:center}
.how{position:absolute;left:425px;top:391px;color:var(--white);font-size:15px}
.dots span{position:absolute;left:1104px;width:12px;height:12px;border:2px solid var(--white);border-radius:50%}

/* about */
.about{top:600px;height:642px}
.eyebrow{font-size:14px;color:var(--yellow);font-weight:500}
.about h2{position:absolute;left:100px;top:145px;font-size:30px;line-height:40px;font-weight:700}
.about p{position:absolute;left:100px;top:250px;width:430px;font-size:12.5px;line-height:23px;color:var(--grey)}
.stat{position:absolute;top:400px;width:178px;height:142px;display:flex;flex-direction:column;align-items:center;justify-content:center;color:var(--white)}
.stat strong{font-size:40px;font-weight:600;line-height:44px}
.stat span{font-size:10px}
.ring{position:absolute;left:708px;top:133px;width:382px;height:382px;border-radius:50%;background:var(--yellow)}
.ring .photo{inset:10px 20px 10px 0;border-radius:50%;background:radial-gradient(circle at 55% 40%,#f1e3d4 0%,#cdb7a2 35%,#2f6b6a 75%)}

/* band */
.band{top:1242px;height:563px;text-align:center;color:var(--white)}
.band .photo{background:linear-gradient(180deg,#2a2a2a,#3d3a36 50%,#1d1d1d)}
.band .label{position:absolute;top:180px;width:100%;font-size:14px;font-weight:500}
.band h2{position:absolute;top:215px;left:0;width:100%;font-size:38px;line-height:50px;font-weight:400}
.band .btn{left:535px;top:378px;width:130px;height:46px}

/* services */
.services{top:1805px;height:645px;text-align:center}
.services .label{position:absolute;top:98px;width:100%;font-size:12px;font-weight:500;letter-spacing:.4px}
.services h2{position:absolute;top:122px;width:100%;font-size:23px;font-weight:600}
.card{position:absolute;top:195px;width:333px;height:293px;background:var(--white);box-shadow:0 2px 12px rgba(0,0,0,.12);text-align:left;padding:30px 0 0 40px}
.card h3{font-size:15px;line-height:20px;font-weight:600;margin-bottom:12px}
.card li{list-style:none;font-size:11.5px;line-height:23.5px;color:var(--grey);padding-left:18px;position:relative}
.card li::before{content:"";position:absolute;left:2px;top:8px;width:7px;height:4px;border-left:2px solid var(--yellow);border-bottom:2px solid var(--yellow);transform:rotate(-45deg)}
.services .btn.dark{left:505px;top:525px;width:192px;height:48px;background:var(--grey);color:var(--white)}

/* steps */
.steps{top:2450px;height:562px;color:var(--white)}
.steps .photo{background:linear-gradient(90deg,#161616,#2b2723 50%,#121212)}
.steps h2{position:absolute;left:72px;top:115px;font-size:38px;line-height:50px;font-weight:600}
.steps .lead{position:absolute;left:72px;top:238px;width:380px;font-size:24px;line-height:32px;font-weight:300}
.steps .btn{left:78px;top:369px;width:154px;height:48px}
.step{position:absolute;left:590px;width:440px}
.step .num{position:absolute;left:0;top:8px;width:48px;height:48px;border:2px solid var(--yellow);border-radius:50%;display:flex;align-items:center;justify-content:center;font-weight:600;font-size:17px}
.step h3{margin-left:74px;font-size:19px;font-weight:600}
.step p{margin-left:76px;margin-top:10px;font-size:11.5px;line-height:21px;color:#d6d6d6}

/* clients */
.clients{top:3012px;height:428px;text-align:center}
.clients .label{position:absolute;top:105px;width:100%;font-size:12px;font-weight:500;letter-spacing:.4px}
.logo{position:absolute;font-size:21px;color:#555;font-weight:500;transform:translateX(-50%);white-space:nowrap}

/* quote */
.quote{top:3440px;height:442px;background:var(--yellow)}
.quote blockquote{position:absolute;left:228px;top:125px;width:790px;font-size:26px;line-height:40px;font-weight:300}
.avatar{position:absolute;left:232px;top:290px;width:70px;height:70px;border-radius:50%;background:#9fd3e6;border:3px solid var(--white)}
.who{position:absolute;left:332px;top:306px}
.who b{display:block;font-size:14px;font-weight:600}
.who span{font-size:11px}
.arrow{position:absolute;top:198px}

/* contact */
.contact{top:3882px;height:448px;color:var(--white);text-align:center}
.contact .photo{background:linear-gradient(90deg,#1a1a1a,#3b3833 50%,#1a1a1a)}
.contact h2{position:absolute;top:83px;width:100%;font-size:19px;font-weight:600}
.contact .sub{position:absolute;top:109px;width:100%;font-size:14px;font-weight:300}
.field{position:absolute;height:48px;background:var(--white);color:#888;font-size:11px;text-align:left;padding:17px 22px}
.contact .btn{left:487px;top:348px;width:225px;height:47px}

/* footer */
.footer{top:4330px;height:455px;background:var(--white)}
.footer .brand{left:75px;top:100px;color:var(--grey)}
.col{position:absolute;top:92px;font-size:12px;line-height:23px;color:var(--grey)}
.col h4{font-size:15px;font-weight:500;color:var(--ink);margin-bottom:8px}
.news{position:absolute;left:882px;top:128px;width:218px;border-bottom:1px solid var(--line);padding-bottom:6px;font-size:11.5px;color:var(--grey)}
.agree{position:absolute;left:882px;top:166px;font-size:11.5px;color:var(--grey)}
.agree::before{content:"";display:inline-block;width:11px;height:11px;border:1px solid #aaa;margin-right:9px;vertical-align:-1px}
.agree u{color:var(--ink);font-weight:500}
.bottom{position:absolute;left:0;top:335px;width:1200px;height:50px;border-top:1px solid var(--line);border-bottom:1px solid var(--line)}
.bottom nav{position:absolute;left:75px;top:18px;display:flex;gap:32px;font-size:9px;font-weight:600}
.follow{position:absolute;left:906px;top:14px;font-size:15px;font-weight:500}
.soc{position:absolute;top:17px;width:14px;height:14px;background:var(--grey);border-radius:50%}
.copy{position:absolute;top:424px;width:100%;text-align:center;font-size:9.5px}
.up{position:absolute;left:1087px;top:410px;width:34px;height:34px;border-radius:50%;background:var(--yellow);display:flex;align-items:center;justify-content:center}
</style>
</head>
<body>

<header class="hero">
  <div class="photo" role="img" aria-label="Photo of smiling colleagues reviewing documents and a tablet at a desk"></div>
  <div class="shade"></div>
  <div class="brand"><i></i>HR Tandem Consulting</div>
  <nav class="nav"><span class="on">Home</span><span>What We Do</span><span>How It Work</span><span>Our Clients</span><span>About Us</span></nav>
  <div class="btn" style="left:966px;top:23px;width:158px;height:49px">Get in touch</div>
  <h1>HR Tandem Consulting is the<br>solution to all your HR issues<b>.</b></h1>
  <div class="sub">We are a one-stop-shop &nbsp;providing a variety of services</div>
  <div class="btn" style="left:143px;top:378px;width:175px;height:48px">Contact sales</div>
  <div class="play"><svg width="14" height="14" viewBox="0 0 14 14"><path d="M3 1l10 6-10 6z" fill="#fff"/></svg></div>
  <div class="how">How it Works</div>
  <div class="dots"><span style="top:317px;background:var(--yellow);border-color:var(--yellow)"></span><span style="top:345px"></span><span style="top:374px"></span></div>
</header>

<section class="about">
  <div class="eyebrow abs" style="left:100px;top:110px">HR Tandem Consulting</div>
  <h2>We assess your HR needs<br>&amp; offer ongoing HR Services.</h2>
  <p>We have worked with some of the most innovative companies in Silicon Valley, across a broad range of industries, and we're proud to grow our client list every year. HR Tandem's experienced professionals help implement and maintain best practices, allowing our clients to focus on their core competencies.</p>
  <div class="stat" style="left:100px;background:var(--grey)"><strong style="color:var(--yellow)">15+</strong><span>Years of Experience</span></div>
  <div class="stat" style="left:303px;background:var(--yellow)"><strong>200+</strong><span>Locations Worldwide</span></div>
  <div class="ring"><div class="photo" role="img" aria-label="Photo of a smiling woman working on a laptop"></div></div>
</section>

<section class="band">
  <div class="photo" role="img" aria-label="Photo of a diverse team of professionals standing together in an office"></div>
  <div class="label">YOUR HUMAN RESOURCES SOLUTION.</div>
  <h2>Whether you have a specific HR<br>need or seek relief by outsourcing<br>altogether, we have you covered</h2>
  <div class="btn">About us</div>
</section>

<section class="services">
  <div class="label">SOME OF OUR SERVICES</div>
  <h2>WHAT CAN WE HELP YOU WITH?</h2>
  <div class="card" style="left:75px"><h3>We Help<br>Setup</h3><ul>
    <li>Select and implement an HRIS system</li><li>Create Company Handbook</li><li>Write termination procedure</li><li>Set up benefits services</li><li>Set up workers comp vendor</li><li>Create job descriptions for current<br>and anticipated roles</li></ul></div>
  <div class="card" style="left:433px"><h3>Managing HR<br>Functions /Recruiting</h3><ul>
    <li>Onboarding/Offboarding</li><li>Employee relations</li><li>Investigations</li><li>Leave administration</li><li>Immigration liaison</li><li>Compensation management</li><li>Full cycle recruitment</li></ul></div>
  <div class="card" style="left:792px"><h3>Recurring<br>Procedures</h3><ul>
    <li>Review handbook annually</li><li>Roll out training (required and soft<br>skills training)</li><li>Write offer letters</li><li>Handle employee data and files</li><li>Conduct I-9 audits</li><li>Handle merit and review bonuses</li></ul></div>
  <div class="btn dark">View all services</div>
</section>

<section class="steps">
  <div class="photo" role="img" aria-label="Dark photo of a professional in a meeting"></div>
  <h2>The Fastest Way<br>to Set You Up</h2>
  <div class="lead">Tell us what you need and we'll get you up and running in just a few days.</div>
  <div class="btn">Get started</div>
  <div class="step" style="top:117px"><div class="num">1</div><h3>Discovery Call</h3><p>You'll speak to the person we recommend to verify that it's a good match before you sign up, so that you have that extra level of confidence in who you'll be working with.</p></div>
  <div class="step" style="top:263px"><div class="num">2</div><h3>Placement Process</h3><p>You'll speak to the person we recommend to verify that it's a good match before you sign up, so that you have that extra level of confidence in who you'll be working with.</p></div>
  <div class="step" style="top:395px"><div class="num">3</div><h3>Onboarding &amp; Nurturing</h3><p>You'll speak to the person we recommend to verify that it's a good match before you sign up, so that you have that extra level of confidence in who you'll be working with.</p></div>
</section>

<section class="clients">
  <div class="label">TRUSTED BY THOUSANDS OF COMPANIES</div>
  <div class="logo" style="left:170px;top:186px">Orvane</div>
  <div class="logo" style="left:323px;top:186px">Lumetric</div>
  <div class="logo" style="left:503px;top:186px">Taskloom</div>
  <div class="logo" style="left:682px;top:186px">Norbank</div>
  <div class="logo" style="left:860px;top:186px">Quillo</div>
  <div class="logo" style="left:1010px;top:186px">Averly &amp; Co.</div>
  <div class="logo" style="left:217px;top:273px">benefyt</div>
  <div class="logo" style="left:393px;top:273px">kidstreet</div>
  <div class="logo" style="left:586px;top:273px">Harlow Crest</div>
  <div class="logo" style="left:775px;top:273px">Delmar Vins</div>
  <div class="logo" style="left:950px;top:273px">Brandt&amp;Partners</div>
</section>

<section class="quote">
  <svg class="arrow" style="left:74px" width="28" height="52" viewBox="0 0 28 52"><path d="M26 2L2 26l24 24" fill="none" stroke="#111" stroke-width="2"/></svg>
  <svg class="arrow" style="left:1097px" width="28" height="52" viewBox="0 0 28 52"><path d="M2 2l24 24L2 50" fill="none" stroke="#111" stroke-width="2"/></svg>
  <blockquote>I consistently received glowing remarks about our virtual assistant from our customer base. The standard HR Tandem Consulting upholds is premium.</blockquote>
  <div class="avatar" role="img" aria-label="Portrait photo of the reviewer"></div>
  <div class="who"><b>MAYA CORRIN</b><span>Customer Service Manager, Pixelhive</span></div>
</section>

<section class="contact">
  <div class="photo" role="img" aria-label="Dark photo of a team working together at a table"></div>
  <h2>LET'S START THE CONVERSATION.</h2>
  <div class="sub">Tell us what you need so you can meet your new staff.</div>
  <div class="field" style="left:117px;top:176px;width:476px">For my business</div>
  <div class="field" style="left:615px;top:176px;width:476px">Company</div>
  <div class="field" style="left:117px;top:252px;width:226px">First name</div>
  <div class="field" style="left:366px;top:252px;width:226px">Last name</div>
  <div class="field" style="left:615px;top:252px;width:226px">Email</div>
  <div class="field" style="left:864px;top:252px;width:226px">Phone</div>
  <div class="btn">Get started</div>
</section>

<footer class="footer">
  <div class="brand"><i></i>HR Tandem Consulting</div>
  <div class="col" style="left:373px"><h4>Company</h4>About Us<br>Our History<br>Contact<br>News &amp; Views<br>Board of Directors<br>Privacy Policy</div>
  <div class="col" style="left:602px"><h4>Address</h4>120 Harbor Street, 18th Fl.<br>New York, NY 10004
    <h4 style="margin-top:22px">Contact Info</h4>Call:234-555-0140<br>info@hrtandemconsulting.com</div>
  <div class="col" style="left:882px"><h4>Newsletter</h4></div>
  <div class="news">
    <svg width="12" height="9" viewBox="0 0 12 9" style="margin-right:8px"><rect x=".5" y=".5" width="11" height="8" fill="none" stroke="#4a4a4a"/><path d="M.5.5L6 5l5.5-4.5" fill="none" stroke="#4a4a4a"/></svg>Enter Your Email Address
    <svg width="14" height="8" viewBox="0 0 14 8" style="position:absolute;right:0;top:4px"><path d="M0 4h12M9 1l3 3-3 3" fill="none" stroke="#4a4a4a"/></svg>
  </div>
  <div class="agree">I agree to the <u>Privacy Policy.</u></div>
  <div class="bottom">
    <nav><span>HOME</span><span>WHAT WE DO</span><span>HOW IT WORK</span><span>OUR CLIENTS</span><span>ABOUT US</span></nav>
    <div class="follow">Follow Us</div>
    <span class="soc" style="left:1043px"></span><span class="soc" style="left:1063px"></span><span class="soc" style="left:1083px"></span><span class="soc" style="left:1103px"></span>
  </div>
  <div class="copy">Copyright 2021 HR Tandem Consulting</div>
  <div class="up"><svg width="12" height="14" viewBox="0 0 12 14"><path d="M6 13V2M1 7l5-5 5 5" fill="none" stroke="#111" stroke-width="1.5"/></svg></div>
</footer>

</body>
</html>
```